New Business Card for our Indoor Golf Training Facility

We are looking for designs for a new business card for our indoor golf training facility. Attached is our logo, our logo with our slogan, and here is our elevator pitch (What makes us different from the others) not sure if all the info will fit on one card, maybe you can condense the elevator pitch? here is the info

Elevator Pitch
We work with serious golfers and those that want to be serious golfers…
to make you better, faster, at all phases of the game…
We use the same state-of-the-art technology as professional golfers…
which produces data sets that shows your improvement in real time.
Our facility is available 24/7 to our members, which allows you to improve on your time.

our website: www.birchpinlinks.com

Target Market(s)

Golfers

Font styles to use
Serif
Sans Serif

Colors
ec1f27
f59195
fbd4d5
919191
d3d3d3
1b1b1b

Requirements
Must have
• our logo or our logo with the slogan, elevator pitch (can be condensed or shortened)

```html
<!DOCTYPE html>
<html lang="en">
<head>
<meta charset="utf-8">
<title>Birch Pin Links – Business Card</title>
<link rel="stylesheet" href="https://fonts.googleapis.com/css2?family=Open+Sans:wght@400;600;700&family=PT+Sans:ital,wght@0,400;0,700;1,700&display=swap">
<style>
  :root {
    --backdrop: #8a5532;
    --card-light: #dcbb93;
    --card-mid: #c99f73;
    --card-dark: #b98c60;
    --ink: #1b1b1b;
    --rule: #2a2118;
  }
  * { box-sizing: border-box; margin: 0; padding: 0; }
  html, body { width: 1200px; height: 900px; overflow: hidden; }
  body {
    background: var(--backdrop);
    position: relative;
    color: var(--ink);
    font-family: "Open Sans", sans-serif;
  }
  .card {
    position: absolute;
    background: linear-gradient(160deg, var(--card-light) 0%, var(--card-mid) 55%, var(--card-dark) 100%);
    box-shadow: 2px 4px 10px rgba(0,0,0,0.35);
  }
  .card--front { left: 329px; top: 90px; width: 556px; height: 344px; }
  .card--back  { left: 329px; top: 469px; width: 560px; height: 344px; }

  .brand { position: absolute; left: 0; right: 0; top: 68px; text-align: center; }
  .brand__name { display: block; font-weight: 700; font-size: 36px; line-height: 1; letter-spacing: -0.5px; }
  .brand__slogan { display: block; margin-top: 8px; font-family: "PT Sans", sans-serif; font-size: 13px; line-height: 1; }

  .contact { position: absolute; left: 0; right: 0; top: 166px; text-align: center; }
  .contact__name { font-size: 21px; font-weight: 600; line-height: 24px; }
  .contact__title { font-size: 16px; line-height: 20px; }
  .contact__rule { width: 150px; height: 1px; background: var(--rule); margin: 5px auto 4px; }
  .contact__line { font-size: 16px; line-height: 20px; }

  .pitch { position: absolute; left: 0; right: 0; top: 70px; text-align: center; font-family: "PT Sans", sans-serif; }
  .pitch__heading { font-family: "Open Sans", sans-serif; font-weight: 700; font-size: 18px; margin-bottom: 21px; }
  .pitch__para { font-size: 16.5px; line-height: 20px; margin-bottom: 8px; }
  .pitch__rule { width: 454px; height: 1px; background: var(--rule); margin: 17px auto 14px; }
  .pitch__cta { font-size: 16.5px; }
  .pitch__cta em { font-weight: 700; }
</style>
</head>
<body>
  <section class="card card--front">
    <div class="brand">
      <span class="brand__name">Birch Pin Links</span>
      <span class="brand__slogan">Train Smart. Swing Sure. Score Lower.</span>
    </div>
    <div class="contact">
      <p class="contact__name">Daniel Hargrove</p>
      <p class="contact__title">Managing Director</p>
      <div class="contact__rule"></div>
      <p class="contact__line">555-201-3388</p>
      <p class="contact__line">www.birchpinlinks.com</p>
      <div class="contact__rule"></div>
      <p class="contact__line">1480 W. Alder Ave. Unit B4</p>
      <p class="contact__line">Maple Grove, OH 45900</p>
    </div>
  </section>

  <section class="card card--back">
    <div class="pitch">
      <h2 class="pitch__heading">ELEVATOR PITCH</h2>
      <p class="pitch__para">We work with serious golfers and those that want to be serious golfers…<br>to make you better, faster, at all phases of the game…</p>
      <p class="pitch__para">We use the same state-of-the-art technology as professional golfers…<br>which produces data sets that shows your improvement in real time.</p>
      <p class="pitch__para">Our facility is available 24/7 to our members, which allows<br>you to improve on your time.</p>
      <div class="pitch__rule"></div>
      <p class="pitch__cta">Visit <em>www.birchpinlinks.com</em> for more details.</p>
    </div>
  </section>
</body>
</html>
```